Website for data analytics startup

I have a landing page up at http://quenvo.io I need to expand this into a basic company website. I want something similar to this design: http://kelmarix.com/examples/carousel/

I need HTML and CSS for each of the designs, once they are approved. I need the following pages: home page, product, team, blog, and a design for the container of our demo application.

Our logo is attached and also available here: https://files.dravistore.net/quenvo.public/LOGO-colour.png I would like the website branding to match the logo.

I need a blog design with CSS that works with Tumblr.

Our app can be seen at http://demo.quenvo.io Please don't change the look of the network graph itself, only the surrounding content.

For CSS, I want you to use Bootstrap or Foundation as the starting point.

Target Market(s)

Sales and marketing, strategy

Industry/Entity Type

It Company

Coding

Coded - Design and coding required

Number of Pages Required

4 page

Font styles to use
Serif
Sans Serif

Requirements
Must have
• Clean, healthy appeal. Must work well with our logo. Blog page must integrate with Tumblr easily. Must use Bootstrap or Foundation for the starting point of the HTML/CSS.
Should not have
• Ugly crap, flash looking design. NO FLASH.

```html
<!DOCTYPE html>
<html lang="en">
<head>
<meta charset="utf-8">
<title>Quenvo — Data Analytics</title>
<link href="https://fonts.googleapis.com/css2?family=Open+Sans:wght@400;600;700&display=swap" rel="stylesheet">
<style>
:root{
  --green:#5cb32b;
  --navy:#1d3f5e;
  --teal-band:#1f4a62;
  --ink:#333;
  --muted:#777;
  --line:#e2e2e2;
  --footer:#0d0d0d;
  --footer-bar:#1a1a1a;
  --white:#fff;
}
*{box-sizing:border-box;margin:0;padding:0}
html,body{width:726px;height:1200px;overflow:hidden}
body{font-family:"Open Sans",Arial,sans-serif;color:var(--ink);background:var(--white);font-size:6px;line-height:1.5;position:relative}

/* hero */
.hero{position:absolute;top:0;left:0;width:726px;height:363px;overflow:hidden}
.hero-photo{position:absolute;inset:0;background:linear-gradient(120deg,#24506b 0%,#3d7388 45%,#7fa6b0 70%,#2c5369 100%)}
.hero-shade{position:absolute;inset:0;background:linear-gradient(180deg,rgba(10,30,45,.55) 0%,rgba(10,30,45,.25) 40%,rgba(10,30,45,.45) 100%)}
.topbar{position:absolute;top:8px;right:70px;display:flex;gap:14px;color:#d8e6ec;font-size:6px}
.brand{position:absolute;top:34px;left:72px;color:var(--white);font-weight:600;font-size:17px;letter-spacing:1px;text-transform:uppercase}
.nav{position:absolute;top:42px;left:322px;display:flex;gap:4px}
.nav a{color:var(--white);text-decoration:none;font-size:8px;padding:4px 12px;border-radius:2px}
.nav a.active{background:var(--green)}
.hero-title{position:absolute;top:226px;left:0;width:100%;text-align:center;color:var(--white);font-size:25px;font-weight:700;letter-spacing:.5px;line-height:1.2}
.hero-text{position:absolute;top:268px;left:163px;width:400px;text-align:center;color:#e6eef2;font-size:6.5px}
.hero-btns{position:absolute;top:326px;left:0;width:100%;display:flex;justify-content:center;gap:14px}
.btn{display:inline-block;font-size:7px;color:var(--white);padding:5px 14px;border-radius:2px;text-decoration:none}
.btn-dark{background:#2a3a44;border:1px solid #fff}
.btn-green{background:var(--green);border:1px solid var(--green)}
.hero-arrow{position:absolute;top:172px;width:14px;height:20px;background:rgba(0,0,0,.55)}
.hero-arrow svg{display:block;margin:5px auto}

/* about */
.about{position:absolute;top:363px;left:0;width:726px;height:244px;text-align:center}
.section-title{font-size:13px;font-weight:600;color:#2b2b2b;letter-spacing:.3px;line-height:1.3}
.about .section-title{margin-top:44px}
.about-text{width:480px;margin:6px auto 0;color:var(--muted);font-size:5.5px}
.features{display:flex;justify-content:center;gap:44px;margin-top:22px}
.feature{width:100px}
.feature-icon{width:32px;height:32px;border-radius:50%;background:var(--navy);margin:0 auto;display:flex;align-items:center;justify-content:center}
.feature-line{width:80px;height:1px;background:var(--green);margin:8px auto 6px}
.feature h3{font-size:7.5px;font-weight:600;color:#333}
.feature p{font-size:5px;color:var(--muted);margin-top:3px}

/* domain */
.domain{position:absolute;top:607px;left:0;width:726px;height:163px;background:var(--teal-band);text-align:center;color:var(--white)}
.domain .section-title{color:var(--white);margin-top:33px}
.domain-text{width:480px;margin:8px auto 0;color:#c3d3dc;font-size:5.5px}
.search{width:460px;margin:16px auto 0;display:flex;height:18px}
.search-input{flex:1;background:var(--white);color:#666;font-size:6px;text-align:left;padding:5px 8px;white-space:nowrap}
.search-select{width:80px;background:var(--white);border-left:1px solid var(--line);color:#666;font-size:5.5px;padding:5px 6px;text-align:left;white-space:nowrap}
.search-btn{width:22px;background:var(--green);display:flex;align-items:center;justify-content:center}

/* projects */
.projects{position:absolute;top:770px;left:0;width:726px;height:193px}
.projects .section-title{position:absolute;top:48px;left:72px}
.project{position:absolute;left:78px;width:330px;display:flex;gap:8px}
.project-thumb{width:72px;height:44px;flex:none;background:linear-gradient(135deg,#7fb6d9,#d9e8f1 60%,#a7c7da)}
.project h4{font-size:5.5px;font-weight:600;color:#222}
.project p{font-size:5px;color:var(--muted)}
.project .date{color:var(--green);font-size:5px;margin-top:2px}
.form-card{position:absolute;top:66px;left:485px;width:160px;height:112px;border:1px solid #ccc;background:var(--white);padding:8px}
.field{height:9px;border:1px solid #d6d6d6;margin-bottom:5px;font-size:4.5px;color:#999;padding:1px 3px;line-height:6px}
.field-area{height:40px}
.form-submit{display:block;margin:4px auto 0;width:30px;height:9px;background:#1d2b36;color:var(--white);font-size:4.5px;text-align:center;line-height:9px}
.form-tail{position:absolute;bottom:-8px;left:18px}

/* footer */
.footer{position:absolute;top:963px;left:0;width:726px;height:216px;background:var(--footer);color:#aaa}
.fcol{position:absolute;top:20px}
.fcol h5{color:var(--white);font-size:7px;font-weight:700;margin-bottom:10px;letter-spacing:.3px}
.fcol li{list-style:none;font-size:5px;margin-bottom:4px}
.blog-item{display:flex;gap:5px;margin-bottom:7px;width:120px}
.blog-thumb{width:22px;height:16px;flex:none;background:linear-gradient(135deg,#5a6e7d,#a9b8c2)}
.blog-item p{font-size:4.8px;line-height:1.4}
.tweet{display:flex;gap:5px;margin-bottom:7px;width:120px}
.tweet-dot{width:8px;height:8px;flex:none;border-radius:50%;background:#3a3a3a;margin-top:1px}
.tweet p{font-size:4.8px;line-height:1.4}
.footer-bar{position:absolute;top:1179px;left:0;width:726px;height:21px;background:var(--footer-bar);color:#888;font-size:5px}
.copyright{position:absolute;top:7px;left:72px}
.social{position:absolute;top:5px;right:70px;display:flex;gap:3px}
.social span{width:10px;height:10px;background:#2b7bbf}
.social span:last-child{background:#d9482b}
</style>
</head>
<body>

<header class="hero">
  <div class="hero-photo" role="img" aria-label="Business team reviewing analytics charts in an office"></div>
  <div class="hero-shade"></div>
  <div class="brand">Quenvo</div>
  <div class="topbar"><span>Call us now: +1 (555) 010-7731</span><span>hello@quenvo.io</span></div>
  <nav class="nav">
    <a class="active" href="#">Home</a><a href="#">Projects</a><a href="#">Analytics</a><a href="#">Research</a><a href="#">Reports</a><a href="#">Contact us</a>
  </nav>
  <div class="hero-arrow" style="left:0"><svg width="6" height="10" viewBox="0 0 6 10"><path d="M5 1L1 5l4 4" stroke="#fff" fill="none" stroke-width="1.4"/></svg></div>
  <div class="hero-arrow" style="right:0"><svg width="6" height="10" viewBox="0 0 6 10"><path d="M1 1l4 4-4 4" stroke="#fff" fill="none" stroke-width="1.4"/></svg></div>
  <h1 class="hero-title">WELCOME TO QUENVO</h1>
  <p class="hero-text">We turn scattered sales and marketing records into clear answers, mapping every link between your buyers, partners and markets so your team can act with confidence and plan ahead.</p>
  <div class="hero-btns"><a class="btn btn-dark" href="#">More Details</a><a class="btn btn-green" href="#">More Details</a></div>
</header>

<section class="about">
  <h2 class="section-title">WE ARE A DATA ANALYTICS STARTUP COMPANY</h2>
  <p class="about-text">Our small team builds tools that read your market like a network. We gather public and private signals, link them together and show where the real chances lie, so strategy and sales teams can move faster with less guesswork every single day.</p>
  <div class="features">
    <div class="feature">
      <div class="feature-icon"><svg width="14" height="14" viewBox="0 0 14 14"><rect x="2" y="1" width="10" height="12" fill="none" stroke="#fff" stroke-width="1.2"/><path d="M4 5h6M4 8h6M4 11h4" stroke="#fff" stroke-width="1"/></svg></div>
      <div class="feature-line"></div>
      <h3>vitae dicta sunt lcatio</h3>
      <p>Clean reports built from the data you already own today.</p>
    </div>
    <div class="feature">
      <div class="feature-icon"><svg width="14" height="14" viewBox="0 0 14 14"><path d="M2 12V7M6 12V4M10 12V2" stroke="#fff" stroke-width="2"/></svg></div>
      <div class="feature-line"></div>
      <h3>vitae dicta sunt lcatio</h3>
      <p>Live charts that track each market as it keeps moving.</p>
    </div>
    <div class="feature">
      <div class="feature-icon"><svg width="14" height="14" viewBox="0 0 14 14"><circle cx="6" cy="6" r="4" fill="none" stroke="#fff" stroke-width="1.4"/><path d="M9 9l4 4" stroke="#fff" stroke-width="1.6"/></svg></div>
      <div class="feature-line"></div>
      <h3>vitae dicta sunt lcatio</h3>
      <p>Search every link between buyers, partners and rivals.</p>
    </div>
    <div class="feature">
      <div class="feature-icon"><svg width="14" height="14" viewBox="0 0 14 14"><rect x="1" y="2" width="12" height="8" fill="none" stroke="#fff" stroke-width="1.2"/><path d="M5 12h4M7 10v2" stroke="#fff" stroke-width="1.2"/></svg></div>
      <div class="feature-line"></div>
      <h3>vitae dicta sunt lcatio</h3>
      <p>A simple dashboard your whole team can open anywhere.</p>
    </div>
  </div>
</section>

<section class="domain">
  <h2 class="section-title">DO YOU HAVE THE RIGHT DOMAIN? SEARCH FOR IT NOW</h2>
  <p class="domain-text">Find the right address for your next project in seconds. Type a name, choose an ending and we will tell you right away if it is free, along with similar options worth a look before you decide and register it.</p>
  <div class="search">
    <div class="search-input">Enter Your Domain Name Here and Start Searching</div>
    <div class="search-select">.COM (Free SEO Tools) ▾</div>
    <div class="search-btn"><svg width="9" height="9" viewBox="0 0 9 9"><circle cx="3.8" cy="3.8" r="2.6" fill="none" stroke="#fff" stroke-width="1.1"/><path d="M5.8 5.8L8.3 8.3" stroke="#fff" stroke-width="1.2"/></svg></div>
  </div>
</section>

<section class="projects">
  <h2 class="section-title">OUR PROJECTS</h2>
  <article class="project" style="top:76px">
    <div class="project-thumb" role="img" aria-label="Analytics dashboard project preview"></div>
    <div>
      <h4>Market map for a regional retail group and partners</h4>
      <p>We linked store sales, supplier data and local trends into one view, helping the group spot growth areas and trim weak lines within a single quarter of work.</p>
      <p class="date">Posted 12 March 2014</p>
    </div>
  </article>
  <article class="project" style="top:134px">
    <div class="project-thumb" role="img" aria-label="Research network project preview"></div>
    <div>
      <h4>Lead scoring network for a software sales team</h4>
      <p>Our graph tools ranked thousands of leads by their real ties to current clients, giving the sales team a short list that closed faster than before.</p>
      <p class="date">Posted 28 February 2014</p>
    </div>
  </article>
  <form class="form-card">
    <div class="field">Your Name</div>
    <div class="field">Select Subject ▾</div>
    <div class="field field-area">Your Message</div>
    <span class="form-submit">SUBMIT</span>
    <svg class="form-tail" width="14" height="9" viewBox="0 0 14 9"><path d="M0 0L7 8L14 0" fill="#fff" stroke="#ccc"/><path d="M1 0h12" stroke="#fff" stroke-width="2"/></svg>
  </form>
</section>

<footer class="footer">
  <div class="fcol" style="left:97px">
    <h5>INFORMATION</h5>
    <ul><li>› HOME</li><li>› PRODUCTS</li><li>› ANALYTICS</li><li>› RESEARCH</li><li>› REPORTS</li><li>› CONTACT US</li></ul>
  </div>
  <div class="fcol" style="left:225px">
    <h5>LATEST BLOG</h5>
    <div class="blog-item"><div class="blog-thumb" role="img" aria-label="Blog post thumbnail"></div><p>Five signs your sales data is hiding new markets</p></div>
    <div class="blog-item"><div class="blog-thumb" role="img" aria-label="Blog post thumbnail"></div><p>How network graphs change the way we plan</p></div>
    <div class="blog-item"><div class="blog-thumb" role="img" aria-label="Blog post thumbnail"></div><p>Our first year building a data startup</p></div>
  </div>
  <div class="fcol" style="left:392px">
    <h5>LATEST TWEETS</h5>
    <div class="tweet"><span class="tweet-dot"></span><p>New release out today with faster graph loading</p></div>
    <div class="tweet"><span class="tweet-dot"></span><p>Join our free webinar on market mapping next week</p></div>
    <div class="tweet"><span class="tweet-dot"></span><p>Thanks to everyone who tried the demo this month</p></div>
  </div>
  <div class="fcol" style="left:547px">
    <h5>QUICK LINKS</h5>
    <ul><li>› OUR TEAM</li><li>› PRODUCT TOUR</li><li>› LIVE DEMO</li><li>› PRICING</li><li>› BLOG</li><li>› SUPPORT</li></ul>
  </div>
</footer>
<div class="footer-bar">
  <span class="copyright">Copyright © 2014 Quenvo Inc. All rights reserved.</span>
  <div class="social"><span></span><span></span><span></span><span></span><span></span><span></span></div>
</div>

</body>
</html>
```